Quorbelline.io - Please redesign to make it look better from current design

We already have the current website, that you can access but we think it can improve from current version.
Quorbelline is a cryptocurrency hedge fund that allow you to participate in the hedge fund with cryptocurrency such as eth.
At current phase, we are doing an ICO, then we want to make sure that the website it looks professional, beautiful and trustable enough for investors after looking at our website.
Target Market(s)
Investors
Industry/Entity Type
Investment
Coding
Coded - Design and coding required
Number of Pages Required
1 page
Look and feel
Each slider illustrates characteristics of the customer's brand and the style your logo design should communicate.

```html
<!DOCTYPE html>
<html lang="en">
<head>
<meta charset="utf-8">
<title>Quorbelline – Digital Asset Management</title>
<link rel="stylesheet" href="https://fonts.googleapis.com/css2?family=Comfortaa:wght@400;700&family=Quicksand:wght@400;500;600;700&display=swap">
<style>
:root{
  --navy:#0c2a69;
  --navy-deep:#0a2260;
  --white:#ffffff;
  --soft:#c9d3ea;
  --ink:#1b1f2a;
  --grey-light:#e9ecf1;
}
*{box-sizing:border-box;margin:0;padding:0}
html,body{width:1200px;height:3390px;overflow:hidden;background:var(--navy)}
body{font-family:"Quicksand",sans-serif;color:var(--white)}
.row{display:flex;width:1200px;height:678px}
.panel{position:relative;width:600px;height:678px;overflow:hidden}
.panel--navy{background:var(--navy);text-align:center}
.fill{position:absolute;inset:0}
.heading{font-family:"Comfortaa",sans-serif;font-weight:400;font-size:56px;letter-spacing:1px}
.subheading{font-family:"Quicksand",sans-serif;font-weight:600;font-size:22px}
.body-text{font-size:14.5px;line-height:27px;color:var(--soft)}
.btn{display:inline-block;border:2px solid var(--white);border-radius:30px;color:var(--white);font-weight:600;font-size:20px;padding:12px 38px;text-decoration:none;box-shadow:0 0 0 3px rgba(255,255,255,.15)}
.block{position:absolute;left:0;right:0;padding:0 50px}

/* hero */
.brand{position:absolute;left:74px;top:26px;display:flex;align-items:center;gap:10px;color:var(--navy);font-family:"Quicksand",sans-serif;font-weight:700;font-size:20px}
.brand__dot{width:34px;height:34px;border-radius:50%;background:var(--navy)}
.menu-btn{position:absolute;right:50px;top:44px;width:40px;height:40px;border:2px solid var(--white);display:flex;flex-direction:column;justify-content:center;align-items:center;gap:5px}
.menu-btn span{display:block;width:18px;height:2px;background:var(--white)}

/* chart */
.chart{position:absolute;left:0;top:0}

/* team */
.team{position:absolute;left:111px;top:267px;display:flex;gap:8px}
.member{width:188px;height:260px;background:var(--white);text-align:center;color:var(--ink)}
.member__photo{height:203px;background:linear-gradient(160deg,#d7dbe2,#8a929e)}
.member__name{font-weight:700;font-size:13px;margin-top:13px}
.member__role{font-size:11px;color:#555;margin-top:4px}
.pager{position:absolute;top:555px;left:0;right:0;display:flex;justify-content:center;gap:10px}
.pager span{width:40px;height:28px;border:2px solid var(--white);display:flex;align-items:center;justify-content:center}
.pager span.active{background:var(--white)}

/* distribution */
.dist-diagram{position:absolute;inset:0}
.dist-title{position:absolute;top:116px;left:0;right:0;text-align:center;color:var(--navy);font-weight:600;font-size:24px}
.dist-sub{position:absolute;top:152px;left:0;right:0;text-align:center;color:var(--navy);font-size:15px}
.dist-label{position:absolute;font-size:10.5px;line-height:13px;font-style:italic;color:var(--navy);text-decoration:underline;font-weight:600;white-space:nowrap}
.dist-note{position:absolute;top:536px;left:0;right:0;text-align:center;color:var(--navy);font-weight:700;font-size:17px;line-height:22px;text-decoration:underline}

/* contact */
.location{display:flex;align-items:center;justify-content:center;gap:12px;font-weight:600;font-size:22px}
</style>
</head>
<body>

<section class="row hero">
  <div class="panel">
    <div class="fill" role="img" aria-label="Photo of a businessman looking out over a city skyline through office windows" style="background:linear-gradient(180deg,#d9dde3 0%,#a7b0bc 55%,#7f8a99 100%)"></div>
    <div class="brand"><span class="brand__dot"></span>quorbelline</div>
  </div>
  <div class="panel panel--navy">
    <div class="menu-btn"><span></span><span></span><span></span></div>
    <div class="block" style="top:150px">
      <h1 class="heading">Quorbelline</h1>
      <p class="subheading" style="margin-top:28px">Digital Asset Management</p>
      <p class="body-text" style="margin-top:14px">Quorbelline enable companies and investors to facilities business operation in modern digital world, including asset management on hedge fund strategy model.</p>
      <a class="btn" style="margin-top:30px">READ MORE</a>
    </div>
  </div>
</section>

<section class="row definition">
  <div class="panel panel--navy">
    <div class="block" style="top:160px">
      <h2 class="heading">Definition</h2>
      <p class="body-text" style="margin-top:22px">Quorbelline process and manages on hedge fund strategy models which invests in a diversified portfolio of blockchain tokens. Blockchain tokens are emerging which add a monetary incentive layer to p2p protocols and facilitate equity crowdfunding that anyone in the world can participate in. This means open source software developers can monetize their networks at the protocol level and users of the network are the equity owners of the network. For this conditions, returns will go to holders of the tokens.</p>
      <a class="btn" style="margin-top:24px">READ MORE</a>
    </div>
  </div>
  <div class="panel">
    <div class="fill" role="img" aria-label="Photo of hands typing on a laptop with charts on screen" style="background:linear-gradient(150deg,#f3f5f8 0%,#dfe4ea 50%,#c4cbd4 100%)"></div>
    <svg class="chart" width="600" height="678" viewBox="0 0 600 678">
      <g>
        <rect x="54" y="422" width="36" height="91" fill="#0c2a69"/>
        <rect x="131" y="384" width="36" height="129" fill="#0b0b0d"/>
        <rect x="204" y="337" width="36" height="176" fill="#0c2a69"/>
        <rect x="280" y="294" width="36" height="219" fill="#0b0b0d"/>
        <rect x="357" y="262" width="36" height="251" fill="#0c2a69"/>
        <rect x="432" y="215" width="36" height="298" fill="#0b0b0d"/>
        <rect x="506" y="174" width="36" height="339" fill="#0c2a69"/>
      </g>
      <g font-family="Quicksand, sans-serif" font-size="14" fill="#1b1f2a" text-anchor="middle">
        <text x="72" y="540">2001</text><text x="149" y="540">2002</text><text x="222" y="540">2003</text>
        <text x="298" y="540">2004</text><text x="375" y="540">2005</text><text x="450" y="540">2006</text>
        <text x="524" y="540">2007</text>
      </g>
    </svg>
  </div>
</section>

<section class="row team-row">
  <div class="panel">
    <div class="fill" role="img" aria-label="Black and white photo of a businessman overlaid with city towers" style="background:linear-gradient(180deg,#eceef1 0%,#9ea4ad 55%,#3c424b 100%)"></div>
  </div>
  <div class="panel panel--navy">
    <div class="block" style="top:100px">
      <h2 class="heading">Our Team</h2>
      <p class="body-text" style="margin-top:16px">Quorbelline enable companies and investors to facilities business operation in modern digital world.</p>
    </div>
    <div class="team">
      <div class="member">
        <div class="member__photo" role="img" aria-label="Portrait of the director"></div>
        <p class="member__name">Tavin Morell</p>
        <p class="member__role">Director</p>
      </div>
      <div class="member">
        <div class="member__photo" role="img" aria-label="Portrait of the technical advisor"></div>
        <p class="member__name">Dario Kellen</p>
        <p class="member__role">Technical advisor</p>
      </div>
    </div>
    <div class="pager">
      <span><svg width="16" height="10" viewBox="0 0 16 10"><path d="M15 5H3M6 1L2 5l4 4" stroke="#fff" stroke-width="2" fill="none"/></svg></span>
      <span class="active"><svg width="16" height="10" viewBox="0 0 16 10"><path d="M1 5h12M10 1l4 4-4 4" stroke="#0c2a69" stroke-width="2" fill="none"/></svg></span>
    </div>
  </div>
</section>

<section class="row process">
  <div class="panel panel--navy">
    <div class="block" style="top:165px">
      <h2 class="heading">Process</h2>
      <p class="subheading" style="margin-top:26px">Hedge Fund Model</p>
      <p class="body-text" style="margin-top:10px">Quorbelline run on closed-end fund (CEF) model which offers its shares to investors and utilize the fund to speculate and invest in the innovative blockchain tokens. Quorbelline will charge on upfront annual operation fee 4% of the money raised during the ICO. After that, the fund will charge a quarterly performance of 50% on the net profit made.</p>
      <a class="btn" style="margin-top:24px">READ MORE</a>
    </div>
  </div>
  <div class="panel">
    <div class="fill" role="img" aria-label="Soft light photo of business documents on a desk" style="background:linear-gradient(160deg,#f7f8fa 0%,#e3e7ec 60%,#d2d8e0 100%)"></div>
    <svg class="dist-diagram" width="600" height="678" viewBox="0 0 600 678">
      <circle cx="307" cy="352" r="158" fill="none" stroke="#0c2a69" stroke-width="1.5" stroke-dasharray="3 5"/>
      <circle cx="307" cy="352" r="84" fill="#0c2a69" stroke="#fff" stroke-width="6"/>
      <text x="307" y="360" text-anchor="middle" font-family="Quicksand, sans-serif" font-weight="700" font-size="20" fill="#fff">quorbelline</text>
      <g stroke="#fff" stroke-width="4">
        <circle cx="190" cy="270" r="38" fill="#0c2a69"/>
        <circle cx="425" cy="270" r="38" fill="#0c2a69"/>
        <circle cx="190" cy="445" r="38" fill="#0c2a69"/>
        <circle cx="425" cy="445" r="38" fill="#0c2a69"/>
      </g>
      <g fill="#fff">
        <path d="M190 252a18 18 0 1 1-18 18h18z"/>
        <path d="M425 252a18 18 0 1 1-18 18h18z" opacity=".5"/><path d="M425 252v18l15 10a18 18 0 0 0-15-28z"/>
        <path d="M190 427a18 18 0 1 0 18 18h-18z"/>
        <path d="M425 427a18 18 0 0 0 0 36z"/>
      </g>
    </svg>
    <p class="dist-title">Net Profit Distribution</p>
    <p class="dist-sub">50 % of net profit is distributed to investors</p>
    <span class="dist-label" style="left:40px;top:206px">0 – 5 % net profit &gt; 0% performance fee</span>
    <span class="dist-label" style="left:332px;top:206px">5 – 10% net profit &gt; 5% performance fee</span>
    <span class="dist-label" style="left:40px;top:502px">10-15 % net profit &gt; 10% performance fee</span>
    <span class="dist-label" style="left:332px;top:502px">&gt; 15% net profit &gt; 15% performance fee</span>
    <p class="dist-note">The remainder (50% minus performance fee, so at least 35%) is<br>reinvested</p>
  </div>
</section>

<section class="row contact">
  <div class="panel">
    <div class="fill" role="img" aria-label="Street map showing the office location" style="background:linear-gradient(120deg,#aecbf0 0%,#dfe6ea 40%,#eef0e6 70%,#d4e6d4 100%)"></div>
  </div>
  <div class="panel panel--navy">
    <div class="block" style="top:165px">
      <h2 class="heading">Contact Us</h2>
      <p class="location" style="margin-top:26px">
        <svg width="18" height="24" viewBox="0 0 18 24"><path d="M9 1a8 8 0 0 0-8 8c0 6 8 14 8 14s8-8 8-14a8 8 0 0 0-8-8zm0 11a3 3 0 1 1 0-6 3 3 0 0 1 0 6z" fill="#c9d3ea"/></svg>
        Location
      </p>
      <p class="body-text" style="margin-top:14px;line-height:24px">Rooms 08-12, 9/F, North Tower,<br>Meridian Trade Centre, Lantern Quay, 44 Harlow Road,<br>Eastgate, Kowloon.</p>
      <p class="subheading" style="margin-top:42px">FOR MORE INFORMATION</p>
      <a class="btn" style="margin-top:14px;background:var(--white);color:var(--navy);padding:12px 26px">DOWNLOAD WHITEPAPER</a>
    </div>
  </div>
</section>

</body>
</html>
```